Bright Trails, Strong Spirits Poster for American Indian Older Adults

We need am 11" x 17" poster designed for a health outreach project designed to reach older U.S. American Indians. The materials developed through this project will be distributed to American Indian and Alaska Native tribes, communities and tribal-serving organizations across the U.S. (more than 500 different tribes). If we find a successful design we will work with that designer to produce at least one other item we need design work for using the same look/feel and maybe other materials for this project. (more work!). The poster will include a set of facts (bulleted list on the attached document) that we would like presented in an "infographic" style. The design must be reflective of the American Indian culture and designed with older adults (65 and older) in mind. Imagery plays a strong role in the American Indian culture in the U.S. images of the heart, water, feathers, circle of life, etc. If you use photos of people they must include older adults and they must be American Indian (Native American). We prefer deep earth tones for the color scheme. The design must take into account design principles for older adults: 1. Try not to put colored font on colored background 2. Ensure high contrast for text 3. Font style should be sans serif, not cursive,decorative or heavily stylized because it is harder to read 4. Avoid using all caps 5. Don't print sideways or on top of images, shaded, backgrounds, etc. 6. All images should related specifically to the content of the text and be culturally appropriate for both older adults and American Indians. The final design should be easy to read and appeal to older American Indian adults. We need to incorporate three logos on the poster towards the bottom they should not be the center/focus of the poster. We also need to include a statement about who produced the materials- that can be very small below the logos at the bottom of the poster. We've attached the text for the poster and three logo files (note one is solid blue- we will finalize that after the document design is selected but need a placeholder for that logo.

Target Market(s)

Older adult (65 and older) American Indian and Alaska Natives and their family members in tribes, communities and tribal-serving organizations across the US

Font styles to use
Sans Serif

Requirements
Must have
• Must adhere to good design principles for older adults (listed in project description)
• Must feature culturally appropriate/targeted imagery and design look and feel

```html
<!DOCTYPE html>
<html lang="en">
<head>
<meta charset="utf-8">
<title>Bright Trails, Strong Spirits</title>
<link rel="stylesheet" href="https://fonts.googleapis.com/css2?family=Montserrat:ital,wght@0,400;0,500;0,600;0,700;1,700&family=Playfair+Display:wght@700;800&display=swap">
<style>
  :root {
    --band: #c7a27a;
    --cream: #f4e6c6;
    --gold: #d3a866;
    --amber: #a87a45;
    --umber: #5a3f27;
    --earth: #2e2116;
    --red: #9a1c22;
    --ink: #3a2418;
    --white: #ffffff;
    --rule: #c9a772;
    --dash: #b8944f;
  }
  * { margin: 0; padding: 0; box-sizing: border-box; }
  html, body { width: 775px; height: 1200px; overflow: hidden; background: var(--white); }
  .poster {
    position: relative;
    width: 775px;
    height: 1200px;
    overflow: hidden;
    font-family: "Montserrat", Arial, sans-serif;
    background: var(--white);
  }
  .pattern-band {
    position: absolute; left: 0; top: 0; width: 775px; height: 47px;
    background: linear-gradient(180deg, #d2b08a, var(--band));
  }
  .photo {
    position: absolute; left: 0; top: 47px; width: 775px; height: 1098px;
    background:
      radial-gradient(ellipse 260px 520px at 560px 640px, rgba(30,20,12,0.75), rgba(30,20,12,0) 70%),
      linear-gradient(180deg, var(--cream) 0%, #ecd8ae 22%, var(--gold) 36%, var(--amber) 52%, var(--umber) 72%, var(--earth) 100%);
  }
  .subtitle {
    position: absolute; left: 15px; top: 64px;
    color: var(--red); font-weight: 700; font-size: 26px; line-height: 34px;
  }
  .headline {
    position: absolute; left: 15px; top: 178px;
    font-family: "Playfair Display", Georgia, serif;
    color: var(--ink); font-weight: 800; font-size: 56px; line-height: 58px;
    letter-spacing: -1.5px;
  }
  .stat { position: absolute; left: 0; width: 420px; color: var(--white); }
  .stat .icon { position: absolute; left: 24px; top: 4px; width: 72px; height: 60px; }
  .stat .text { position: absolute; left: 112px; top: 0; width: 300px; }
  .stat .lead { font-size: 14px; font-weight: 500; line-height: 18px; }
  .stat .big { font-size: 31px; font-weight: 700; line-height: 34px; }
  .stat .note { font-size: 15px; font-weight: 500; line-height: 18px; }
  .rule { position: absolute; left: 0; height: 2px; background: var(--rule); }
  .risk {
    position: absolute; left: 112px; top: 900px; width: 305px;
    color: var(--white); font-weight: 700; font-size: 15px; line-height: 19px;
  }
  .cta {
    position: absolute; left: 118px; top: 1052px; width: 480px;
    color: var(--white); font-weight: 700; font-style: italic; font-size: 16px; line-height: 24px;
  }
  .dash-rule {
    position: absolute; left: 110px; top: 1130px; width: 665px; height: 6px;
    background: repeating-linear-gradient(90deg, var(--dash) 0 3px, transparent 3px 5px);
    opacity: 0.85;
  }
  .footer {
    position: absolute; left: 0; top: 1145px; width: 775px; height: 55px;
    background: var(--white); border-top: 1px solid #e6e0d6;
    display: flex; align-items: center; gap: 28px; padding-left: 18px;
  }
  .partner { display: flex; align-items: center; gap: 8px;
    font-family: "Montserrat", Arial, sans-serif; font-weight: 700; font-size: 15px; color: var(--ink); }
  .partner .mark { width: 12px; height: 12px; border-radius: 50%; background: var(--red); }
</style>
</head>
<body>
<main class="poster">
  <div class="pattern-band" role="img" aria-label="Woven geometric band in tan and rust tones"></div>
  <div class="photo" role="img" aria-label="Sepia photograph of an elderly couple seen from behind, standing on a beach at sunset, with a faint portrait of an elder in a feather headdress blended into the sky"></div>

  <h2 class="subtitle">The River of Life Flows<br>Through the Heart,<br>Protecting the Mind and Body</h2>
  <h1 class="headline">Bright Trails,<br>Strong Spirits …</h1>

  <section class="stat" style="top:468px">
    <svg class="icon" viewBox="0 0 72 60" aria-hidden="true"><rect x="4" y="14" width="62" height="36" rx="6" fill="#fff"/></svg>
    <div class="text">
      <div class="big">5.7 Million</div>
      <div class="note">Americans have<br>Alzheimer’s disease</div>
    </div>
  </section>
  <div class="rule" style="top:548px;width:410px"></div>

  <section class="stat" style="top:570px">
    <svg class="icon" viewBox="0 0 72 60" aria-hidden="true">
      <path d="M36 56 L10 30 A14 14 0 0 1 36 12 A14 14 0 0 1 62 30 Z" fill="none" stroke="#fff" stroke-width="2.5" stroke-linejoin="round"/>
      <polyline points="6,34 24,34 29,24 35,44 41,18 46,34 66,34" fill="none" stroke="#fff" stroke-width="2.5" stroke-linejoin="round"/>
    </svg>
    <div class="text">
      <div class="lead">Alzheimer’s is the</div>
      <div class="big">6th</div>
      <div class="note">leading cause of Death</div>
    </div>
  </section>
  <div class="rule" style="top:650px;width:400px"></div>

  <section class="stat" style="top:676px">
    <svg class="icon" viewBox="0 0 72 60" aria-hidden="true" fill="#fff">
      <circle cx="36" cy="6" r="4" fill="#d38a4a"/><rect x="32" y="11" width="8" height="12" rx="2" fill="#d38a4a"/>
      <circle cx="28" cy="24" r="3.5"/><rect x="25" y="28" width="7" height="10" rx="2"/>
      <circle cx="44" cy="24" r="3.5"/><rect x="41" y="28" width="7" height="10" rx="2"/>
      <circle cx="20" cy="40" r="3.5"/><rect x="17" y="44" width="7" height="12" rx="2"/>
      <circle cx="36" cy="40" r="3.5"/><rect x="33" y="44" width="7" height="12" rx="2"/>
      <circle cx="52" cy="40" r="3.5"/><rect x="49" y="44" width="7" height="12" rx="2"/>
      <circle cx="6" cy="40" r="3.5"/><rect x="3" y="44" width="7" height="12" rx="2"/>
      <circle cx="66" cy="40" r="3.5"/><rect x="63" y="44" width="7" height="12" rx="2"/>
    </svg>
    <div class="text">
      <div class="big">1 in 10</div>
      <div class="note">People age 65 and older<br>has Alzheimer’s</div>
    </div>
  </section>
  <div class="rule" style="top:756px;width:410px"></div>

  <section class="stat" style="top:782px">
    <svg class="icon" viewBox="0 0 72 60" aria-hidden="true"><circle cx="36" cy="32" r="26" fill="#fff"/></svg>
    <div class="text">
      <div class="big">1 in 3</div>
      <div class="note">American Indians over 65<br>develop dementia, including<br>Alzheimer’s</div>
    </div>
  </section>
  <div class="rule" style="top:880px;width:105px"></div>

  <p class="risk">Elders with diabetes, heart disease, or high blood pressure have a much higher risk of developing Alzheimer’s or other dementias</p>

  <p class="cta">Make an appointment with your doctor today to talk<br>about how to keep your mind and heart healthy.</p>

  <div class="dash-rule"></div>

  <footer class="footer">
    <div class="partner"><span class="mark"></span>Stateline Health</div>
    <div class="partner">Cedar Circle Elders Alliance</div>
  </footer>
</main>
</body>
</html>
```